Sports Nutrition line needs new label look/feel

We need a new label design for "Volrex",our Sports Nutrition line of vitamins, nutraceuticals, protein powders, and performance endurance products. We would like to see two separate designs, one blue and one red, as these are the two colors we are torn between. The labels should have the look/feel of a sports or fitness label, bold coloring, lettering, and even some use of holographic foiling.
Brands we would be similar to those found on gymstackhub.com and strongpathmarket.com. Brands we like in particular are KTW and Velmora.

Target Market(s)

Fitness enthusiasts,athletes, health nuts..

Industry/Entity Type

Nutrition

Font styles to use
Sans Serif
Decorative
Script

Colors
ec1f27
0692cd
0355a3
3276b5
f04a50

Requirements
Must have
• -Fitness look/feel
• -bold colors (preferably red and blue)
• -use of icons (eye health, brain, health, etc.)
• -"Fit" in "VolREX" must stand out
• -use tagline "Building Healthy Bodies"
Nice to have
• -holographic foiling elements
• -try to incorporate a molecular element (like those shown in the example labels)
Should not have
• -Light, calming colors
• -difficult to read fonts

```html
<!DOCTYPE html>
<html lang="en">
<head>
<meta charset="utf-8">
<title>Volrex Grape Seed Extract Label</title>
<link href="https://fonts.googleapis.com/css2?family=Open+Sans:ital,wght@0,400;0,600;0,700;0,800;1,700;1,800&display=swap" rel="stylesheet">
<style>
  :root {
    --page: #ffffff;
    --label-blue: #0d5fae;
    --label-blue-deep: #0a4f97;
    --stripe: rgba(255,255,255,0.05);
    --band-light: #2d8fd3;
    --silver: #d9dee3;
    --icon-fill: #3d9fe0;
    --icon-line: #eef6fc;
    --orange: #ef6a22;
    --white: #ffffff;
  }
  * { margin: 0; padding: 0; box-sizing: border-box; }
  html, body { width: 1200px; height: 1143px; overflow: hidden; background: var(--page); }
  body { position: relative; font-family: "Open Sans", Arial, sans-serif; color: var(--white); }

  .label {
    position: absolute; left: 130px; top: 100px; width: 940px; height: 943px;
    overflow: hidden;
    background:
      repeating-linear-gradient(-55deg, var(--stripe) 0 2px, transparent 2px 22px),
      linear-gradient(180deg, var(--label-blue) 0%, var(--label-blue-deep) 100%);
  }
  .label-art { position: absolute; inset: 0; }

  .brand-name {
    position: absolute; left: 0; right: 0; top: 212px;
    text-align: center; font-weight: 800; font-size: 104px; letter-spacing: 2px; line-height: 1;
  }
  .tagline {
    position: absolute; left: 0; right: 0; top: 360px;
    text-align: center; font-weight: 600; font-size: 23px; letter-spacing: 1px;
  }
  .product-name {
    position: absolute; left: 0; right: 0; top: 490px;
    text-align: center; font-weight: 700; font-size: 70px; line-height: 1;
  }
  .product-type {
    position: absolute; left: 0; right: 0; top: 588px;
    text-align: center; font-weight: 700; font-size: 52px; line-height: 1;
  }
  .benefit {
    position: absolute; left: 70px; top: 752px; width: 560px;
    text-align: center; font-weight: 400; font-size: 30px; line-height: 1.3;
  }
  .benefit strong { font-weight: 700; }
  .supply {
    position: absolute; left: 650px; top: 700px; width: 280px;
    text-align: center; line-height: 1.1;
  }
  .supply-count { font-weight: 700; font-size: 58px; display: block; }
  .supply-days { font-weight: 400; font-size: 24px; display: block; margin-top: 6px; }
  .supply-kind { font-weight: 800; font-style: italic; font-size: 20px; display: block; margin-top: 4px; }
</style>
</head>
<body>
  <main class="label">
    <svg class="label-art" width="940" height="943" viewBox="0 0 940 943">
      <defs>
        <radialGradient id="leftGlow" cx="0" cy="0.18" r="1">
          <stop offset="0" stop-color="#e6f6ff"/>
          <stop offset="0.35" stop-color="#5ab9ee"/>
          <stop offset="1" stop-color="#1f7fc6"/>
        </radialGradient>
        <radialGradient id="rightGlow" cx="1" cy="0.55" r="1">
          <stop offset="0" stop-color="#e6f6ff"/>
          <stop offset="0.35" stop-color="#5ab9ee"/>
          <stop offset="1" stop-color="#1f7fc6"/>
        </radialGradient>
        <linearGradient id="silverEdge" x1="0" y1="0" x2="0" y2="1">
          <stop offset="0" stop-color="#f4f6f8"/>
          <stop offset="0.5" stop-color="#9aa3ab"/>
          <stop offset="1" stop-color="#eef1f3"/>
        </linearGradient>
        <linearGradient id="bannerFill" x1="0" y1="0" x2="1" y2="0">
          <stop offset="0" stop-color="#3aa0de"/>
          <stop offset="1" stop-color="#1f86cc"/>
        </linearGradient>
      </defs>

      <rect class="band-top" x="0" y="0" width="940" height="16" fill="#2d8fd3"/>
      <rect class="band-bottom" x="0" y="888" width="940" height="55" fill="#2d8fd3"/>
      <rect x="0" y="884" width="940" height="4" fill="#7fc4ee"/>

      <path class="side-panel" d="M0,16 L180,16 Q250,420 115,884 L0,884 Z" fill="url(#leftGlow)" role="img" aria-label="Light rays glowing from the top left corner"/>
      <path d="M180,16 Q250,420 115,884" fill="none" stroke="url(#silverEdge)" stroke-width="16"/>

      <path class="side-panel" d="M940,16 L790,16 Q700,440 790,884 L940,884 Z" fill="url(#rightGlow)" role="img" aria-label="Light rays glowing from the right edge"/>
      <path d="M790,16 Q700,440 790,884" fill="none" stroke="url(#silverEdge)" stroke-width="16"/>

      <g class="benefit-icons" fill="var(--icon-fill)" stroke="var(--silver)" stroke-width="4">
        <circle cx="72" cy="240" r="42"/>
        <circle cx="72" cy="430" r="42"/>
        <circle cx="72" cy="612" r="42"/>
        <circle cx="860" cy="240" r="42"/>
        <circle cx="860" cy="420" r="42"/>
        <circle cx="860" cy="600" r="42"/>
      </g>

      <g class="icon-glyphs" fill="none" stroke="var(--icon-line)" stroke-width="3" stroke-linecap="round" stroke-linejoin="round">
        <g class="icon-joint" role="img" aria-label="Joint health icon">
          <path d="M52,222 L70,242 M70,242 L92,232"/>
          <circle cx="50" cy="219" r="5"/>
          <circle cx="95" cy="230" r="5"/>
          <circle cx="72" cy="246" r="8"/>
          <path d="M72,254 L72,262"/>
        </g>
        <g class="icon-bone" role="img" aria-label="Bone health icon">
          <path d="M56,446 L88,414"/>
          <circle cx="52" cy="444" r="5"/><circle cx="58" cy="450" r="5"/>
          <circle cx="86" cy="410" r="5"/><circle cx="92" cy="416" r="5"/>
        </g>
        <g class="icon-muscle" role="img" aria-label="Muscle strength icon">
          <path d="M50,630 Q52,604 66,596 Q74,592 76,600 L70,604 Q78,618 92,616 Q96,630 80,632 Z"/>
        </g>
        <g class="icon-hair" role="img" aria-label="Hair health icon">
          <path d="M836,256 L884,256"/>
          <path d="M848,254 Q844,238 850,222 M860,254 Q856,236 862,220 M872,254 Q868,238 874,222"/>
        </g>
        <g class="icon-brain" role="img" aria-label="Brain health icon">
          <ellipse cx="860" cy="418" rx="24" ry="17"/>
          <path d="M860,401 L860,435 M846,410 Q852,416 846,424 M874,410 Q868,416 874,424"/>
        </g>
        <g class="icon-eye" role="img" aria-label="Eye health icon">
          <path d="M834,600 Q860,578 886,600 Q860,622 834,600 Z"/>
          <circle cx="860" cy="600" r="7"/>
        </g>
      </g>

      <path d="M60,718 L640,718 L640,720 L612,870 L60,870 Z" fill="#d9dee3"/>
      <path d="M70,728 L628,728 L602,860 L70,860 Z" fill="url(#bannerFill)"/>

      <circle cx="800" cy="815" r="175" fill="#d9dee3"/>
      <circle cx="800" cy="815" r="165" fill="#ef6a22"/>
    </svg>

    <h1 class="brand-name">VOLREX</h1>
    <p class="tagline">BUILDING HEALTHY BODIES</p>
    <h2 class="product-name">GRAPE SEED</h2>
    <p class="product-type">EXTRACT</p>
    <p class="benefit">ANTIOXIDANT FORMULA<br><strong>TO</strong> BOOST IMMUNITY</p>
    <p class="supply">
      <span class="supply-count">90</span>
      <span class="supply-days">DAY SUPPLY</span>
      <span class="supply-kind">DIETARY SUPPLEMENT</span>
    </p>
  </main>
</body>
</html>
```